Wordpress Design For Financial Investment Company

//** NEW WIREFRAME ADDED TO HELP WITH LAYOUT ISSUES. PLEASE REFER TO WIREFRAME IN ATTACHED FILES. NO DESIGN WILL BE CONSIDERED IF IT DOES NOT FOLLOW THE WIREFRAME. **//
//** PLEASE READ THE ENTIRE BRIEF INCLUDING ALL UPDATES TO THE BRIEF. THE CLIENT IS VERY SPECIFIC ABOUT WHAT THEY WANT AND I'VE COVERED SEVERAL THINGS IN THE UPDATES. THERE IS ALSO A VIDEO UPDATE THAT HAS SOME VALUABLE INFORMATION IN IT FOR THIS CONTEST. **//
The client is an investment advisor who needs a new website designed. The current site is http://www.velmorhold.example.
The client wants the site to be green to match the attached logo.
The home page should have relevant images in the rotator. No people hugging! This is a financial investment site, not a family counseling site.
Also, the client wants 4 buttons on the home page to highlight the 4 main areas they focus on:
Investment Advice and Education
General Financial Planning
Retirement Planning
401K Planning
The top right area of the site needs to have their phone number, a call to action, and 2 buttons.
Their phone number is 303-418-7719
The call to action should say something like "Call for a free consultation!"
The buttons need to say:
Login To Your Brokavell Account
Login To Your Quillbrook Account
The final design should communicate professionalism, financial safety and growth.
Main navigation should be:
Home
About Us
Associates
Services
Contact
Mission Statement (Could also be "Our Mission")
This is a site that the client likes: http://www.pkwadvisoryfirm.example/
Updates
The designs should not have:
Newsletter content. A newsletter sign up is fine
Learning Center
Calculators
Stock prices/tickers
The design should have a contact form on the page.
I have talked to my client and have some updates. I did a video update because I thought it would be easier to show what I'm trying to get across.
Reason: I am going to be extending the contest a few more days. I'm still not getting quite what I want and very few people are even trying to follow the creative brief and the updates to it.
PLEASE read the entire brief and the updates. There is also a video I made that explains everything. I've also attached a wireframe.
Thanks!
Target Market(s)
People looking for a high-end financial investment company.
Industry/Entity Type
Investment
Requirements
Must have
- !!FOLLOW THE WIREFRAME FOR LAYOUT!!
!!THEIR LOGO!!
4 buttons to highlight their main practice areas
Phone number in the top right
"Free Consultation" call to action
2 Login buttons in the top right
A contact form on the page.
Should not have
- The designs should not have:
Learning Center
Calculators
Stock prices/tickers

```html
<!DOCTYPE html>
<html lang="en">
<head>
<meta charset="utf-8">
<title>Velmor Financial</title>
<link rel="stylesheet" href="https://fonts.googleapis.com/css2?family=Roboto+Condensed:wght@400;500;700&family=Open+Sans:ital,wght@1,400;1,600;1,700&family=Arimo:wght@400;700&display=swap">
<style>
:root{
  --green-dark:#4a8a6c;
  --green-nav:#3f8466;
  --green-text:#3f8466;
  --green-deep:#1f5c42;
  --mint-band:#d3e3db;
  --hero-bg:#d4e4dc;
  --card-bg:#e6efeb;
  --ink:#444;
  --ink-dark:#3a3a3a;
  --white:#fff;
}
*{box-sizing:border-box;margin:0;padding:0}
html,body{width:1200px;height:1000px;overflow:hidden}
body{position:relative;font-family:"Arimo",Arial,sans-serif;color:var(--ink);
  background:linear-gradient(to bottom,var(--green-dark) 0 338px,var(--mint-band) 338px 897px,var(--green-dark) 897px 1000px)}
.page{position:absolute;left:240px;top:40px;width:720px;height:878px;background:var(--white);box-shadow:0 0 10px rgba(0,0,0,.25)}
.edge{position:absolute;left:240px;width:720px}
.edge-top{top:36px}
.edge-bottom{top:912px}
.top-rule{position:absolute;left:240px;top:58px;width:720px;height:8px;background:#c3d8cd}
.brand{position:absolute;left:558px;top:13px;width:84px;height:84px;border-radius:50%;background:var(--white);border:4px solid #2a2a2a;display:flex;align-items:center;justify-content:center;text-align:center;font-family:"Roboto Condensed",sans-serif;font-weight:700;font-size:13px;line-height:1.1;color:var(--ink-dark)}
.login{position:absolute;top:81px;height:21px;border:1px solid #9a9a9a;border-radius:3px;background:linear-gradient(#f4f4f4,#cfcfcf);font-size:10.5px;color:#555;display:flex;align-items:center;justify-content:center}
.login-a{left:247px;width:87px}
.login-b{left:342px;width:91px}
.cta{position:absolute;right:255px;top:80px;height:28px;display:flex;align-items:baseline;gap:8px;white-space:nowrap;font-family:"Roboto Condensed",sans-serif}
.cta-call{font-size:15px;color:#444}
.cta-phone{font-weight:500;font-size:24px;color:var(--green-text)}
.nav{position:absolute;left:247px;top:112px;width:706px;height:41px;background:var(--green-nav);display:flex}
.nav a{color:var(--white);text-decoration:none;font-size:13px;display:flex;align-items:center;justify-content:center;white-space:nowrap;border-right:1px solid #2f6a50;box-shadow:1px 0 0 #5b9b7d}
.social{position:absolute;right:8px;top:11px;display:flex;gap:7px}
.social span{width:19px;height:19px;border-radius:50%;background:var(--white)}
.hero{position:absolute;left:247px;top:157px;width:706px;height:272px;background:var(--hero-bg);overflow:hidden}
.hero-photo{position:absolute;inset:0}
.hero h1{position:absolute;left:32px;top:30px;width:340px;font-family:"Roboto Condensed",sans-serif;font-weight:500;font-size:23px;line-height:32px;color:var(--ink-dark)}
.hero p{position:absolute;left:33px;top:103px;width:274px;font-size:10.6px;line-height:15px;text-align:justify;color:var(--ink-dark)}
.btn-consult{position:absolute;left:34px;top:179px;width:199px;height:48px;border-radius:4px;background:linear-gradient(#3f8d68,#1f5c42);border:1px solid #174a34;color:var(--white);font-family:"Roboto Condensed",sans-serif;font-weight:500;font-size:20px;display:flex;align-items:center;justify-content:center;box-shadow:0 2px 3px rgba(0,0,0,.3)}
.tagline{position:absolute;left:240px;top:449px;width:720px;text-align:center;font-family:"Open Sans",sans-serif;font-style:italic;font-weight:400;font-size:16px;line-height:24px;color:var(--ink-dark)}
.tagline strong{display:block;font-weight:600;font-size:19px;color:var(--green-text)}
.card{position:absolute;top:517px;width:169px;height:273px;background:var(--card-bg)}
.card h2{position:absolute;left:10px;top:14px;width:130px;font-size:13.5px;line-height:15px;color:var(--green-text);font-weight:700}
.card .thumb{position:absolute;left:0;top:53px;width:169px;height:48px}
.card p{position:absolute;left:10px;top:108px;width:155px;height:135px;overflow:hidden;font-size:9.3px;line-height:13.5px;letter-spacing:-.1px;color:#555}
.read-more{position:absolute;top:249px;height:15px;padding:0 12px 0 5px;background:var(--green-nav);color:var(--white);font-size:9px;line-height:15px;clip-path:polygon(0 0,88% 0,100% 50%,88% 100%,0 100%)}
.profile{position:absolute;left:265px;top:801px;width:102px;height:102px;border-radius:50%;border:3px solid var(--green-nav);background:radial-gradient(circle at 50% 40%,#c79a80,#6a5a52 70%,#3e3a38)}
.about{position:absolute;left:381px;top:818px;width:560px;font-size:9px;line-height:14px;letter-spacing:-.05px;color:#555}
.about em{display:block;margin-top:5px;font-family:"Open Sans",sans-serif;font-weight:700;font-size:11px;color:var(--green-text)}
.footer-nav{position:absolute;top:945px;font-size:9px;color:var(--white);display:flex;gap:5px;white-space:nowrap}
.footer-nav.left{left:246px}
.footer-nav.right{right:247px}
</style>
</head>
<body>
<div class="page"></div>
<svg class="edge edge-top" width="720" height="10" viewBox="0 0 720 10"><polygon fill="#fff" points="0,10 0,4 20,2 40,5 60,1 85,4 110,2 140,5 170,1 200,4 230,2 260,5 290,1 320,3 350,2 380,5 410,1 440,4 470,2 500,5 530,1 560,4 590,2 620,5 650,1 680,4 700,2 720,4 720,10"/></svg>
<div class="top-rule"></div>
<svg class="edge edge-bottom" width="720" height="10" viewBox="0 0 720 10"><polygon fill="#fff" points="0,0 720,0 720,5 700,8 680,5 650,9 620,5 590,8 560,5 530,9 500,5 470,8 440,6 410,9 380,5 350,8 320,6 290,9 260,5 230,8 200,5 170,9 140,5 110,8 85,6 60,9 40,5 20,8 0,5"/></svg>

<div class="brand">Velmor<br>Financial</div>

<div class="login login-a">Brokavell Login</div>
<div class="login login-b">Quillbrook Login</div>
<div class="cta"><span class="cta-call">Call for a free consultation!</span><span class="cta-phone">303-418-7719</span></div>

<nav class="nav">
  <a href="#" style="width:66px">Home</a><a href="#" style="width:83px">About Us</a><a href="#" style="width:92px">Associates</a><a href="#" style="width:79px">Services</a><a href="#" style="width:93px">Our Mission</a><a href="#" style="width:79px">Contact</a>
  <div class="social"><span></span><span></span><span></span><span></span></div>
</nav>

<section class="hero">
  <svg class="hero-photo" width="706" height="272" viewBox="0 0 706 272">
    <defs><linearGradient id="heroTone" x1="0" y1="0" x2="1" y2="0"><stop offset="0" stop-color="#b9c3bf"/><stop offset=".5" stop-color="#e8ecea"/><stop offset="1" stop-color="#5a5e5c"/></linearGradient></defs>
    <polygon points="327,272 440,0 706,0 706,272" fill="#3f8466"/>
    <polygon points="338,272 451,0 706,0 706,272" fill="url(#heroTone)" role="img" aria-label="Photo of a businessman in a white shirt and tie talking on a phone"/>
  </svg>
  <h1>Lorem Ipsum is simply dummy text of the printing and typesetting</h1>
  <p>Lorem Ipsum is simply dummy text of the printing and type-setting industry. Lorem Ipsum has been the industry's standard dummy text ever since the 1500s,</p>
  <div class="btn-consult">FREE Consultation</div>
</section>

<div class="tagline"><strong>Lorem Ipsum is simply dummy text of the printing and typesetting</strong>industry. Lorem Ipsum has been the industry's standard dummy text ever since the 1500s,</div>

<article class="card" style="left:247px">
  <h2>Investment Advice and Education</h2>
  <div class="thumb" role="img" aria-label="Photo of a hand writing on documents" style="background:linear-gradient(90deg,#8a5a3c,#e2d6c8 50%,#9a9088)"></div>
  <p>Lorem Ipsum is simply dummy text of the printing and typesetting industry. Lorem Ipsum has been the industry's standard dummy text ever since the 1500s, when an unknown printer took a galley of type and scrambled it to make a type specimen book. It has survived not only five centuries, but also the leap into electronic typesetting, remaining</p>
  <span class="read-more" style="left:89px">Read More</span>
</article>
<article class="card" style="left:426px">
  <h2>General Financial Planning</h2>
  <div class="thumb" role="img" aria-label="Photo of a pen on green financial charts" style="background:linear-gradient(90deg,#4f7a2c,#9dbb5a 50%,#3c5a24)"></div>
  <p>Lorem Ipsum is simply dummy text of the printing and typesetting industry. Lorem Ipsum has been the industry's standard dummy text ever since the 1500s, when an unknown printer took a galley of type and scrambled it to make a type specimen book. It has survived not only five centuries, but also the leap into electronic typesetting, remaining</p>
  <span class="read-more" style="left:88px">Read More</span>
</article>
<article class="card" style="left:605px">
  <h2>Retirement Planning</h2>
  <div class="thumb" role="img" aria-label="Photo of a green street sign reading Retirement against blue sky" style="background:linear-gradient(180deg,#2f7ab8,#2d7a52)"></div>
  <p>Lorem Ipsum is simply dummy text of the printing and typesetting industry. Lorem Ipsum has been the industry's standard dummy text ever since the 1500s, when an unknown printer took a galley of type and scrambled it to make a type specimen book. It has survived not only five centuries, but also the leap into electronic typesetting, remaining</p>
  <span class="read-more" style="left:89px">Read More</span>
</article>
<article class="card" style="left:784px">
  <h2>401K Planning</h2>
  <div class="thumb" role="img" aria-label="Photo of an investment portfolio document" style="background:linear-gradient(90deg,#b9ab94,#e6dccb 50%,#a89a84)"></div>
  <p>Lorem Ipsum is simply dummy text of the printing and typesetting industry. Lorem Ipsum has been the industry's standard dummy text ever since the 1500s, when an unknown printer took a galley of type and scrambled it to make a type specimen book. It has survived not only five centuries, but also the leap into electronic typesetting, remaining</p>
  <span class="read-more" style="left:87px">Read More</span>
</article>

<div class="profile" role="img" aria-label="Portrait photo of an advisor on the phone"></div>
<div class="about">Lorem Ipsum is simply dummy text of the printing and typesetting industry. Lorem Ipsum has been the industry's standard dummy text ever since the 1500s, when an unknown printer took a galley of type and scrambled it to make a type specimen book. It has survived not only five centuries, but also the leap into electronic typesetting, remaining essentially unchanged. It was popularised in the 1960s with the release of Letraset sheets containing Lorem Ipsum passages, and more recently with desktop publishing software like Aldus PageMaker including<em>Standard Dummy Text</em></div>

<div class="footer-nav left"><span>Home</span><span>I</span><span>About Us</span><span>I</span><span>Associates</span><span>I</span><span>Services</span><span>I</span><span>Our Mission</span><span>I</span><span>Contact</span></div>
<div class="footer-nav right"><span>Privacy</span><span>I</span><span>Terms and conditions</span><span>I</span><span>Dislaimer</span></div>
</body>
</html>
```